Harbor Loom Floors Letterhead

Letterhead used for business reasons. It must be editable and easy to use.

Address is 2715 W. Pelican Lane Englewood FL 34187 - 941.382.6519

```html
<!DOCTYPE html>
<html lang="en">
<head>
<meta charset="utf-8">
<title>Harbor Loom Floors Letterhead</title>
<link rel="stylesheet" href="https://fonts.googleapis.com/css2?family=Open+Sans:wght@400;600&family=Lato:wght@400&family=Manrope:wght@500&display=swap">
<style>
  :root {
    --accent: #e08a2a;
    --text: #6b6b6b;
    --muted: #8a857c;
    --rule: #8d8b80;
    --ink: #333333;
    --paper: #ffffff;
    --backdrop: #e9eaec;
    --deco-light: #f8f8f8;
    --deco-dark: #f0f0f0;
  }
  html, body {
    margin: 0;
    width: 999px;
    height: 1200px;
    overflow: hidden;
    background: var(--backdrop);
  }
  .letterhead {
    position: absolute;
    left: 71px;
    top: 0;
    width: 856px;
    height: 1200px;
    background: var(--paper);
    overflow: hidden;
    font-family: "Open Sans", Arial, sans-serif;
    color: var(--text);
  }
  .brand {
    position: absolute;
    left: 60px;
    top: 86px;
    display: flex;
    align-items: center;
    gap: 10px;
    font-family: "Open Sans", Arial, sans-serif;
    font-weight: 600;
    font-size: 31px;
    color: var(--accent);
    white-space: nowrap;
  }
  .brand-mark {
    width: 14px;
    height: 14px;
    background: var(--accent);
  }
  .company-contact {
    position: absolute;
    left: 584px;
    top: 89px;
    font-family: "Lato", Arial, sans-serif;
    font-size: 13px;
    line-height: 16.5px;
    color: var(--muted);
  }
  .company-contact .row {
    display: flex;
    gap: 5px;
    margin-bottom: 9px;
  }
  .company-contact svg { flex: none; margin-top: 1px; }
  .header-rule {
    position: absolute;
    left: 60px;
    top: 185px;
    width: 732px;
    height: 1px;
    background: var(--rule);
  }
  .sender {
    position: absolute;
    left: 76px;
    top: 274px;
  }
  .sender-name {
    margin: 0;
    font-weight: 600;
    font-size: 23px;
    line-height: 30px;
    color: var(--accent);
  }
  .sender-role {
    margin: 0;
    font-size: 12.5px;
    line-height: 18px;
    color: var(--text);
  }
  .sender-details {
    margin: 14px 0 0;
    padding: 0;
    list-style: none;
    font-size: 14.6px;
    line-height: 24px;
  }
  .sender-details li { display: flex; }
  .sender-details .label {
    width: 30px;
    font-weight: 600;
    color: var(--accent);
  }
  .letter-date {
    position: absolute;
    right: 78px;
    top: 398px;
    font-size: 14.6px;
    line-height: 22px;
  }
  .letter-body {
    position: absolute;
    left: 77px;
    top: 473px;
    width: 702px;
    font-size: 14.2px;
    line-height: 22.4px;
    text-align: justify;
  }
  .letter-body p { margin: 0 0 22.3px; }
  .signature {
    position: absolute;
    left: 92px;
    top: 837px;
    width: 124px;
    height: 78px;
    background: linear-gradient(135deg, #f4f4f4, #e9e9e9);
  }
  .signer-name {
    position: absolute;
    left: 77px;
    top: 926px;
    font-family: "Manrope", Arial, sans-serif;
    font-weight: 500;
    font-size: 21px;
    color: var(--ink);
  }
  .corner-decoration {
    position: absolute;
    left: 529px;
    top: 926px;
    width: 412px;
    height: 412px;
    clip-path: polygon(50% 0, 100% 50%, 50% 100%, 0 50%);
    background: linear-gradient(180deg, var(--deco-light), var(--deco-dark));
  }
  .footer-band { position: absolute; left: 0; top: 1184px; }
</style>
</head>
<body>
  <main class="letterhead">
    <div class="corner-decoration" role="img" aria-label="Faint nested diamond line pattern"></div>

    <svg class="footer-band" width="582" height="16" aria-hidden="true">
      <polygon points="0,0 569,0 582,16 0,16" fill="var(--accent)"/>
    </svg>

    <div class="brand"><span class="brand-mark"></span>Harbor Loom Floors</div>

    <div class="company-contact">
      <div class="row">
        <svg width="16" height="16" viewBox="0 0 16 16"><rect width="16" height="16" rx="2" fill="var(--accent)"/><path d="M5 3.5l1.6 2.2-1 1c.6 1.4 1.6 2.4 3 3l1-1 2.2 1.6-.9 1.8c-3.6-.3-6.5-3.2-6.8-6.8z" fill="#fff"/></svg>
        <span>941.382.6519</span>
      </div>
      <div class="row">
        <svg width="16" height="16" viewBox="0 0 16 16"><rect width="16" height="16" rx="2" fill="var(--accent)"/><path d="M8 3a3.5 3.5 0 0 0-3.5 3.5C4.5 9.2 8 13 8 13s3.5-3.8 3.5-6.5A3.5 3.5 0 0 0 8 3zm0 5a1.5 1.5 0 1 1 0-3 1.5 1.5 0 0 1 0 3z" fill="#fff"/></svg>
        <span>2715 W. Pelican Lane Englewood<br>FL 34187</span>
      </div>
    </div>

    <div class="header-rule"></div>

    <section class="sender">
      <h1 class="sender-name">James Doe</h1>
      <p class="sender-role">Chief Director</p>
      <ul class="sender-details">
        <li><span class="label">A :</span>4986 Northwest Washington, DC 20025</li>
        <li><span class="label">W :</span>www.companywebsite.com</li>
        <li><span class="label">P :</span>+00 123 456 78</li>
        <li><span class="label">M :</span>hello@harborloomfloors.com</li>
      </ul>
    </section>

    <div class="letter-date">12 December, 2025</div>

    <section class="letter-body">
      <p>Lorem ipsum dolor sit amet, consectetuer adipiscing elit, sed diam nonummy nibh euismod tincidunt ut laoreet dolore magna aliquam erat volutpat. Ut wisi enim ad minim veniam, quis nostrud exerci tation ullamcorper suscipit lobortis nisl ut aliquip ex ea commodo consequat. Duis autem vel eum iriure dolor in hendrerit in vulputate velit esse molestie consequat, vel illum dolore eu feugiat nulla facilisis at vero eros et accumsan et iusto odio dignissim qui blandit praesent luptatum zzril delenit augue duis dolore te feugait nulla facilisi.</p>
      <p>Lorem ipsum dolor sit amet, cons ectetuer adipiscing elit, sed diam nonummy nibh euismod tincidunt ut laoreet dolore magna aliquam erat volutpat. Ut wisi enim ad minim veniam, quis nostrud exerci tation ullamcorper suscipit lobortis nisl ut aliquip ex ea commodo consequat.</p>
      <p>Lorem ipsum dolor sit amet, consectetuer adipiscing elit, sed diam nonummy nibh euismod tincidunt ut laoreet dolore magna aliquam eratveniam, quis nostrud exerci tation ullamcorper suscipit lobortis nisl ut aliquip ex ea commodo consequat. Lorem ipsum dolor sit zamet, consectetuer adipiscing elit, sed diam nonummy nibh euismod tincidunt.</p>
    </section>

    <div class="signature" role="img" aria-label="Handwritten signature"></div>
    <div class="signer-name">Mr. Jone Smith</div>
  </main>
</body>
</html>
```